Security and Technology Website - Bold and Confident, Something Unexpected

Maple Wren Systems is launching its first website and we need a great design to bring our brand to life and generate DTC and B2B leads.

We have a good logo, but I am struggling with the creative vision to bring it all together. While our industry is Alarm Systems and Technology, we want to create a site that is more friendly and less 'typical' than your standard IT sites.

It Must:
1. Appeal to both men and women. The logo is a bit masculine, so the colors and icons must soften this.
2. Feel modern - we need to convey that we we use the latest technology.
3. Feel a bit high-end. We are not a budget solution.
4. Have a distinct iconography and photo treatment.
5. Feel layered - not just a series of stacked horizontal modules.

It Should Not:
1. Feel like your typical IT website.

Here are resources to get you started!
• Staging Site:
https://maple-wren-systems.shopfrontdemo.example/
Password: Piper

•Brand Guide: https://www.layoutboard.example/design/QKRmWpLcT4V/hNbq8Yf2-ZsKeRtDw7xp-QE/edit?utm_content=QKRmWpLcT4V&utm_campaign=designshare&utm_medium=link2&utm_source=sharebutton

• Logo and Fonts and Photos: :https://files.cloudlocker.example/folders/7HtPqWmZc3Kd9RbLx2VnYs8FgJe4UoAiT?usp=sharing

• Design Inspiration (don't feel limited by this): https://www.layoutboard.example/design/QKTnHsVbWe8/p7MfRz31xYqLcKdTu9GNBw/edit?utm_content=QKTnHsVbWe8&utm_campaign=designshare&utm_medium=link2&utm_source=sharebutton

______________

The winner will be asked to provide design files and finished PNGs of the overall design file, backgrounds, photo treatments/frames, and icons.

The winner will likely be engaged for a phase 2 to build out a product page.

Industry/Entity Type

Alarm Systems, Home Theatres, and Commercial IT Networking

Number of Pages Required

1 page

Font styles to use
Sans Serif

Colors
0054AA
0677BA
7BADD7
CADEEF
E8F1F8
0094D4
00A9DD
6FCCEA
C7EBF8
E9F6FB
EB3D1F
EC4F4E
F09395
F8D3D4
FCEDEE

Requirements
Must have
• 1. Appeal to both men and women. The logo is a bit masculine, so the colors and icons must soften this. 2. Feel modern - we need to convey that we we use the latest technology. 3. Feel a bit high-end. We are not a budget solution. 4. Have a distinct iconography and photo treatment. 5. Feel layered - not just a series of stacked horizontal modules.
Should not have
• 1. Should not feel like just another IT website.

```html
<!DOCTYPE html>
<html lang="en">
<head>
<meta charset="utf-8">
<title>Maple Wren Systems</title>
<link href="https://fonts.googleapis.com/css2?family=Orbitron:wght@500;600&family=Poppins:wght@400;500;600;700&display=swap" rel="stylesheet">
<style>
:root{
  --blue-deep:#0054AA;--blue:#0094D4;--blue-bright:#00A9DD;--blue-soft:#6FCCEA;--blue-pale:#E9F6FB;
  --red:#EB3D1F;--red-soft:#EC4F4E;--pink:#F09395;--pink-pale:#FCEDEE;
  --ink:#222;--muted:#555;--white:#fff;
}
*{box-sizing:border-box;margin:0;padding:0}
html,body{width:1200px;height:5333px;overflow:hidden}
body{position:relative;font-family:'Poppins',sans-serif;color:var(--ink);background:#fff}
.abs{position:absolute}
.display{font-family:'Orbitron',sans-serif;font-weight:500;color:var(--blue);text-transform:uppercase;letter-spacing:1px}
.btn{position:absolute;display:flex;align-items:center;justify-content:center;font-size:13px;font-weight:600;text-transform:uppercase;color:#fff;background:var(--red);letter-spacing:.5px}
.btn-outline{background:transparent;border:2px solid currentColor}
.ph{position:absolute}
.p{font-size:13px;line-height:20px}
/* hero */
.hero{position:absolute;left:0;top:0;width:1200px;height:600px;background:linear-gradient(100deg,#15161b 0%,#2a2a2e 45%,#4a4038 100%)}
.nav a{color:#fff;font-size:11px;text-decoration:none;text-transform:uppercase;margin-right:18px}
.brand{font-weight:700;color:var(--blue);font-size:13px;line-height:15px;display:flex;align-items:center;gap:8px}
.brand i{width:18px;height:18px;background:var(--red);display:block}
/* cards */
.card{position:absolute;width:332px;background:#fff;box-shadow:0 6px 22px rgba(0,0,0,.12)}
.card .img{height:213px}
.card h3{font-size:16px;font-weight:700;color:var(--blue);text-transform:uppercase;margin:38px 25px 10px}
.card p{font-size:11.5px;line-height:18px;color:var(--muted);margin:0 25px}
.card .more{font-size:12px;color:var(--red);margin:18px 25px 0}
/* features */
.feature{position:absolute;top:2175px;width:190px}
.feature h4{font-size:14px;font-weight:700;text-transform:uppercase;line-height:17px;margin-top:16px}
.feature p{font-size:10.5px;line-height:15px;color:var(--muted);margin-top:10px}
.feature .more{font-size:10px;color:var(--red);margin-top:12px}
/* testimonials */
.quote{position:absolute;width:332px;height:195px;background:#fff;box-shadow:0 6px 22px rgba(0,0,0,.12)}
.quote .av{position:absolute;left:30px;top:58px;width:70px;height:70px;border-radius:50%;background:linear-gradient(135deg,#c9a88c,#6d5a4c);border:3px solid #eee}
.quote .nm{position:absolute;left:112px;top:30px;font-size:11px;font-weight:700}
.quote .st{position:absolute;left:200px;top:26px;color:#f29a2e;font-size:13px;letter-spacing:3px}
.quote .tx{position:absolute;left:112px;top:60px;width:195px;font-size:12px;line-height:20px;color:var(--muted)}
/* form */
.field{position:absolute;background:#fff;border:1px solid #dde;font-size:11px;color:#666;padding:10px 16px}
.footer h5{font-family:'Orbitron',sans-serif;font-weight:500;font-size:17px;color:var(--ink);text-transform:uppercase;margin-bottom:14px}
.footer li{list-style:none;font-size:11px;line-height:22px;color:#333}
</style>
</head>
<body>

<!-- HERO -->
<section class="hero" role="img" aria-label="Dimly lit modern living room"></section>
<div class="abs brand" style="left:82px;top:26px;"><i></i>MAPLE WREN<br>SYSTEMS</div>
<nav class="abs nav" style="left:230px;top:37px;">
  <a>Home</a><a>Electronic Security</a><a>Audio+Video</a><a>Networking+Communication</a><a>Cabling</a>
</nav>
<svg class="abs" style="left:926px;top:34px" width="20" height="20" viewBox="0 0 20 20"><circle cx="8" cy="8" r="6" fill="none" stroke="#fff" stroke-width="2"/><line x1="12.5" y1="12.5" x2="18" y2="18" stroke="#fff" stroke-width="2"/></svg>
<div class="btn" style="left:990px;top:27px;width:125px;height:36px;">Contact Us</div>
<h1 class="abs display" style="left:82px;top:155px;font-size:40px;line-height:50px;">Guard your world<br>with cutting-edge<br>security</h1>
<p class="abs p" style="left:82px;top:313px;width:545px;color:#fff;">Lorem ipsum dolor sit amet, consectetur adipiscing elit. Aliquam nec facilisis nisl.Lorem ipsum dolor sitLorem ipsum dolor sit amet, consectetur adipiscing elit. Aliquam nec facilisis nisl.Lorem ipsum dolor sitLorem ipsum dolor sit amet,</p>
<div class="btn" style="left:82px;top:398px;width:150px;height:34px;">Get a quote</div>
<div class="btn btn-outline" style="left:258px;top:398px;width:222px;height:34px;color:#fff;">Free consultation</div>
<svg class="abs" style="left:716px;top:85px" width="418" height="500" viewBox="0 0 418 500" role="img" aria-label="Woman at a home security touch panel">
  <defs><linearGradient id="g1" x1="0" y1="0" x2="1" y2="1"><stop offset="0" stop-color="#cfd2d6"/><stop offset="1" stop-color="#6a6f77"/></linearGradient></defs>
  <polygon points="209,6 412,100 412,370 209,494 6,370 6,100" fill="url(#g1)" stroke="var(--blue)" stroke-width="10" stroke-linejoin="round"/>
</svg>

<!-- ABOUT -->
<svg class="abs" style="left:98px;top:683px" width="446" height="540" viewBox="0 0 446 540" role="img" aria-label="Woman on a video call at home">
  <defs><linearGradient id="g2" x1="0" y1="0" x2="1" y2="1"><stop offset="0" stop-color="#e7e4df"/><stop offset="1" stop-color="#4c4540"/></linearGradient></defs>
  <polygon points="223,6 440,60 440,330 223,534 6,330 6,60" fill="url(#g2)" stroke="var(--blue)" stroke-width="6" stroke-linejoin="round"/>
</svg>
<svg class="abs" style="left:388px;top:1000px" width="192" height="222" viewBox="0 0 192 222" role="img" aria-label="Portrait of the founder">
  <polygon points="96,4 188,40 188,170 96,218 4,170 4,40" fill="#c7cdd4" stroke="var(--blue)" stroke-width="6" stroke-linejoin="round"/>
</svg>
<div class="ph" style="left:535px;top:1180px;width:80px;height:36px;background:#eef1f5;" role="img" aria-label="Founder's handwritten signature"></div>
<p class="abs" style="left:627px;top:780px;font-size:13px;">About Us</p>
<h2 class="abs display" style="left:627px;top:812px;font-size:40px;">Who we are</h2>
<p class="abs" style="left:627px;top:870px;width:480px;font-size:13px;font-weight:600;color:var(--blue);text-transform:uppercase;line-height:19px;">I founded Maple Wren Systems to bring together technology and honest, reliable service.</p>
<p class="abs p" style="left:627px;top:928px;width:470px;color:#333;">I'm proud to call Tennessee home and even prouder to help keep its homes and businesses secure.<br>Whether it's protecting or elevating your space, my goal is to make technology work for you.<br>Think of us as your friendly, neighborhood tech expert—here to safeguard what matters most.</p>
<div class="btn" style="left:627px;top:1074px;width:276px;height:36px;">Tell us how we can help</div>
<div class="btn btn-outline" style="left:920px;top:1074px;width:158px;height:36px;color:#333;">Learn more</div>

<!-- ELECTRONIC SECURITY -->
<section class="abs" style="left:0;top:1304px;width:1200px;height:580px;background:linear-gradient(180deg,#0f1a30 0%,#1b2a48 100%);" role="img" aria-label="Night view of a modern home exterior"></section>
<h2 class="abs display" style="left:0;top:1385px;width:1200px;text-align:center;font-size:40px;">Electronic security</h2>
<p class="abs p" style="left:270px;top:1443px;width:660px;text-align:center;color:#fff;">Lorem ipsum dolor sit amet, consectetur adipiscing elit. Aliquam nec facilisis nisl.Lorem ipsum dolor sitLorem ipsum dolor sit amet, consectetur adipiscing elit. Aliquam nec facilisis nisl.Lorem</p>
<div class="card" style="left:83px;top:1512px;height:420px;"><div class="img" style="background:linear-gradient(135deg,#e6dfd6,#a9917c);" role="img" aria-label="Woman using a wall alarm keypad"></div><h3>Affordable security</h3><p>Lorem ipsum dolor sit amet, consectetur adipiscing elit. Aliquam nec facilisis nisl.Lorem ipsum dolor sitLorem ipsum dolor sit amet, consectetur adipiscing elit. Aliquam nec facilisis</p><p class="more">Learn more &nbsp;→</p></div>
<div class="card" style="left:433px;top:1512px;height:420px;"><div class="img" style="background:linear-gradient(135deg,#d9d2c8,#6e6357);" role="img" aria-label="Home theatre room with a large screen"></div><h3>Enviable entertainment</h3><p>Lorem ipsum dolor sit amet, consectetur adipiscing elit. Aliquam nec facilisis nisl.Lorem ipsum dolor sitLorem ipsum dolor sit amet, consectetur adipiscing elit. Aliquam nec facilisis</p><p class="more">Learn more &nbsp;→</p></div>
<div class="card" style="left:783px;top:1512px;height:420px;"><div class="img" style="background:linear-gradient(135deg,#e4e8ee,#8a96a6);" role="img" aria-label="Team in a video conference meeting"></div><h3>Connected businesses</h3><p>Lorem ipsum dolor sit amet, consectetur adipiscing elit. Aliquam nec facilisis nisl.Lorem ipsum dolor sitLorem ipsum dolor sit amet, consectetur adipiscing elit. Aliquam nec facilisis</p><p class="more">Learn more &nbsp;→</p></div>
<div class="btn" style="left:533px;top:1965px;width:134px;height:33px;">See more</div>

<!-- CONNECT + PROTECT -->
<section class="abs" style="left:0;top:2030px;width:1200px;height:510px;background:linear-gradient(90deg,var(--pink-pale) 0%,#fff 45%,var(--blue-pale) 100%);"></section>
<h2 class="abs display" style="left:0;top:2078px;width:1200px;text-align:center;font-size:40px;">Connect + protect your world</h2>
<p class="abs" style="left:0;top:2137px;width:1200px;text-align:center;font-size:13px;font-weight:600;color:var(--red);letter-spacing:.5px;">PROTECT YOUR PEOPLE, ASSETS, AND INFORMATION FROM WHATEVER COMES</p>

<svg width="0" height="0" style="position:absolute"><defs>
  <symbol id="shield" viewBox="0 0 90 100"><polygon points="45,3 86,20 86,68 45,97 4,68 4,20" fill="#fff" stroke="var(--blue)" stroke-width="3" stroke-linejoin="round"/><polygon points="45,14 74,26 74,62 45,84 16,62 16,26" fill="var(--red)"/></symbol>
</defs></svg>

<div class="feature" style="left:100px;"><svg width="90" height="100"><use href="#shield"/><rect x="44" y="32" width="16" height="28" fill="none" stroke="#fff" stroke-width="3"/><path d="M28 46h18m-6-6 6 6-6 6" stroke="#fff" stroke-width="3" fill="none"/></svg><h4>Entry &amp; motion<br>sensors</h4><p>Lorem ipsum dolor sit amet, consectetur adipiscing elit. Aliquam nec facilisis nisl.Lo</p><p class="more">Learn more &nbsp;→</p></div>
<div class="feature" style="left:314px;"><svg width="90" height="100"><use href="#shield"/><rect x="34" y="28" width="22" height="34" rx="3" fill="none" stroke="#fff" stroke-width="3"/><circle cx="45" cy="50" r="4" fill="#fff"/></svg><h4>Video<br>doorbells</h4><p>Lorem ipsum dolor sit amet, consectetur adipiscing elit. Aliquam nec facilisis nisl.Lo</p><p class="more">Learn more &nbsp;→</p></div>
<div class="feature" style="left:525px;"><svg width="90" height="100"><use href="#shield"/><rect x="28" y="34" width="32" height="14" rx="3" fill="#fff"/><path d="M40 48v10h-8" stroke="#fff" stroke-width="3" fill="none"/></svg><h4>Security<br>cameras</h4><p>Lorem ipsum dolor sit amet, consectetur adipiscing elit. Aliquam nec facilisis nisl.Lo</p><p class="more">Learn more &nbsp;→</p></div>
<div class="feature" style="left:736px;"><svg width="90" height="100"><use href="#shield"/><circle cx="45" cy="48" r="11" fill="#fff"/></svg><h4 style="text-align:center;width:100px">Pet<br>friendly</h4><p>Lorem ipsum dolor sit amet, consectetur adipiscing elit. Aliquam nec facilisis nisl.Lo</p><p class="more">Learn more &nbsp;→</p></div>
<div class="feature" style="left:947px;"><svg width="90" height="100"><use href="#shield"/><path d="M45 30c8 10 12 16 12 22a12 12 0 0 1-24 0c0-6 4-10 6-14 2 4 3 6 6 7 0-5 0-10 0-15z" fill="#fff"/></svg><h4>Fire &amp; carbon<br>monoxide</h4><p>Lorem ipsum dolor sit amet, consectetur adipiscing elit. Aliquam nec facilisis nisl.Lo</p><p class="more">Learn more &nbsp;→</p></div>
<div class="btn" style="left:523px;top:2472px;width:154px;height:33px;">Contact us</div>

<!-- SAFER HOME -->
<section class="abs" style="left:500px;top:2586px;width:700px;height:580px;background:linear-gradient(90deg,rgba(255,255,255,1) 0%,rgba(220,228,238,.7) 50%,#b9a58d 100%);" role="img" aria-label="Modern house exterior at dusk"></section>
<h2 class="abs display" style="left:83px;top:2597px;font-size:40px;line-height:50px;">A safer home or<br>business is as easy as</h2>
<p class="abs p" style="left:83px;top:2753px;width:540px;color:#333;">Lorem ipsum dolor sit amet, consectetur adipiscing elit. Aliquam nec facilisis nisl.Lorem ipsum dolor sitLorem ipsum dolor sit amet, consectetur adipiscing elit. Aliquam nec facilisis nisl.Lorem ipsum dolor sitLorem ipsum dolor sit amet,</p>
<div class="card" style="left:83px;top:2795px;height:362px;"><div class="img" style="height:187px;background:linear-gradient(135deg,#cfd4da,#5e6670);" role="img" aria-label="Technician showing a quote on a laptop"></div><h3>Build an instant quote</h3><p>Our live-estimate builder will guide you through a few questions to help us understand your needsOur live-estimate builder will guide you</p><p class="more">Learn more &nbsp;→</p></div>
<div class="card" style="left:433px;top:2795px;height:362px;"><div class="img" style="height:187px;background:linear-gradient(135deg,#c9805f,#e8e2dc);" role="img" aria-label="Technicians talking in a brick walled room"></div><h3>Schedule installation</h3><p>Our trained techs are efficient and friendly. Southern-born and raised (and one mid-westerner), we will respect your home and your schedule</p><p class="more">Learn more &nbsp;→</p></div>
<div class="card" style="left:783px;top:2795px;height:362px;"><div class="img" style="height:187px;background:linear-gradient(135deg,#1f2d4a,#9aa8bd);" role="img" aria-label="Hands holding a glowing home security symbol"></div><h3>Stay secure 24/7</h3><p>Monitor your home through the app, receive instant alerts, and rely on professional monitoring services for emergencies</p><p class="more">Learn more &nbsp;→</p></div>
<div class="btn" style="left:518px;top:3190px;width:164px;height:33px;">Get started</div>

<!-- TESTIMONIALS -->
<section class="abs" style="left:0;top:3430px;width:1200px;height:492px;background:linear-gradient(180deg,#fff 0%,#d9dde2 40%,#8e8070 100%);" role="img" aria-label="Bright open-plan living room"></section>
<h2 class="abs display" style="left:0;top:3300px;width:1200px;text-align:center;font-size:40px;line-height:50px;">What client says<br>about us</h2>
<div class="quote" style="left:83px;top:3420px;"><div class="av" role="img" aria-label="Client photo"></div><p class="nm">Lorem</p><p class="st">★★★★★</p><p class="tx">“ Lorem ipsum dolor sit amet consectetur. Mi nibh id quam sit iaculis sit in montes felis. Malesuada augue quis duis odio.”</p></div>
<div class="quote" style="left:83px;top:3650px;"><div class="av" role="img" aria-label="Client photo"></div><p class="nm">Lorem</p><p class="st">★★★★★</p><p class="tx">“ Lorem ipsum dolor sit amet consectetur. Mi nibh id quam sit iaculis sit in montes felis. Malesuada augue quis duis odio.”</p></div>
<div class="quote" style="left:783px;top:3420px;"><div class="av" role="img" aria-label="Client photo"></div><p class="nm">Lorem</p><p class="st">★★★★★</p><p class="tx">“ Lorem ipsum dolor sit amet consectetur. Mi nibh id quam sit iaculis sit in montes felis. Malesuada augue quis duis odio.”</p></div>
<div class="quote" style="left:783px;top:3650px;"><div class="av" role="img" aria-label="Client photo"></div><p class="nm">Lorem</p><p class="st">★★★★★</p><p class="tx">“ Lorem ipsum dolor sit amet consectetur. Mi nibh id quam sit iaculis sit in montes felis. Malesuada augue quis duis odio.”</p></div>
<svg class="abs" style="left:443px;top:3455px" width="316" height="380" viewBox="0 0 316 380" role="img" aria-label="Woman presenting on a video call">
  <polygon points="158,5 311,55 311,255 158,375 5,255 5,55" fill="#b8bcc3" stroke="var(--blue)" stroke-width="8" stroke-linejoin="round"/>
</svg>

<!-- REGISTRATION -->
<section class="abs" style="left:425px;top:4025px;width:775px;height:505px;background:linear-gradient(90deg,var(--red-soft) 0%,var(--pink) 35%,var(--blue-soft) 100%);"></section>
<svg class="abs" style="left:83px;top:4003px" width="470" height="540" viewBox="0 0 470 540" role="img" aria-label="Home theatre room with a projector screen">
  <defs><linearGradient id="g3" x1="0" y1="0" x2="1" y2="1"><stop offset="0" stop-color="#e8c98a"/><stop offset=".5" stop-color="#7a6a5a"/><stop offset="1" stop-color="#2b2622"/></linearGradient></defs>
  <polygon points="235,6 464,60 464,330 235,534 6,330 6,60" fill="url(#g3)" stroke="var(--blue)" stroke-width="8" stroke-linejoin="round"/>
</svg>
<h2 class="abs display" style="left:633px;top:4080px;font-size:40px;color:#2a2a2a;">Registration</h2>
<div class="field" style="left:633px;top:4145px;width:472px;height:40px;">Your Name</div>
<div class="field" style="left:633px;top:4198px;width:230px;height:40px;">E-Mail</div>
<div class="field" style="left:873px;top:4198px;width:232px;height:40px;">Phone</div>
<div class="field" style="left:633px;top:4250px;width:472px;height:40px;">Company</div>
<div class="field" style="left:633px;top:4303px;width:472px;height:105px;">Type Here</div>
<div class="btn" style="left:633px;top:4432px;width:160px;height:36px;">Submit now</div>

<!-- PARTNERS -->
<div class="abs" style="left:0;top:4678px;width:1200px;display:flex;justify-content:space-around;padding:0 80px;font-size:26px;font-weight:600;color:#333;">
  <span>Northgate</span><span>Vantoro</span><span>Lockridge</span><span>Aurelle</span><span>Pembrook</span>
</div>

<!-- NEWSLETTER -->
<div class="abs brand" style="left:245px;top:4905px;font-size:24px;line-height:28px;color:#1d1d1d;gap:14px;"><i style="width:30px;height:30px;"></i>MAPLE WREN<br>SYSTEMS</div>
<p class="abs" style="left:495px;top:4885px;font-size:16px;color:#666;">Subscribe Your News Latter Solutions?</p>
<div class="field" style="left:495px;top:4922px;width:330px;height:44px;padding-top:13px;">Enter Your Email</div>
<div class="btn" style="left:822px;top:4922px;width:178px;height:44px;font-size:16px;">Subscribe</div>

<!-- FOOTER -->
<div class="abs" style="left:0;top:5058px;width:1200px;border-top:1px solid #ddd;"></div>
<div class="abs footer" style="left:243px;top:5088px;"><h5>The quick links</h5><ul><li>Home</li><li>About Us</li><li>Audio+Video</li><li>Networking+Communication</li><li>Electronic Security</li></ul></div>
<div class="abs footer" style="left:510px;top:5088px;width:280px;"><h5>Contact us</h5>
  <ul>
    <li style="display:flex;gap:12px;"><svg width="16" height="20" viewBox="0 0 16 20"><path d="M8 1a6 6 0 0 1 6 6c0 5-6 12-6 12S2 12 2 7a6 6 0 0 1 6-6z" fill="none" stroke="#333" stroke-width="1.5"/><circle cx="8" cy="7" r="2" fill="#333"/></svg><span>Lorem ipsum is simply dummy<br>text Lorem Ipsum Is Simply.</span></li>
    <li style="display:flex;gap:12px;margin-top:6px;"><svg width="16" height="16" viewBox="0 0 16 16"><rect x="1" y="3" width="14" height="10" fill="none" stroke="#333" stroke-width="1.5"/><path d="M1 3l7 6 7-6" fill="none" stroke="#333" stroke-width="1.5"/></svg>hello@maplewren.example</li>
    <li style="display:flex;gap:12px;margin-top:6px;"><svg width="16" height="16" viewBox="0 0 16 16"><path d="M3 1l3 3-2 2c1 3 3 5 6 6l2-2 3 3-2 2C7 15 1 9 1 3z" fill="none" stroke="#333" stroke-width="1.5"/></svg>615.555.0142</li>
  </ul>
</div>
<div class="abs footer" style="left:833px;top:5088px;"><h5>Social links</h5>
  <div style="display:flex;gap:26px;margin-top:4px;">
    <span role="img" aria-label="Social one" style="width:32px;height:32px;border-radius:50%;background:var(--red-soft);display:block"></span>
    <span role="img" aria-label="Social two" style="width:32px;height:32px;border-radius:50%;background:var(--blue-deep);display:block"></span>
    <span role="img" aria-label="Social three" style="width:32px;height:32px;border-radius:50%;background:var(--blue-bright);display:block"></span>
    <span role="img" aria-label="Social four" style="width:32px;height:32px;border-radius:50%;background:var(--red);display:block"></span>
  </div>
</div>
<p class="abs" style="left:0;top:5290px;width:1200px;text-align:center;font-size:11px;color:#333;">© The Maple Wren Systems. All Rights Reserved.</p>

</body>
</html>
```